Solar and battery company needs a mailer brochure

I need a Tri-fold brochure to be mailed the size of the brochure should be 16 inches long by 8.5 inches tall high gloss finish thick paper
use a solid black background the letters should be white in color and when using borders please use red color
first page to say:
BEAT BLACKOUTS SAVE MONEY
You may qualify for a free battery system.
( include a design of the utility grid , solar panels ,battery ,money sign savings just like the PDF File show it )
at the bottom of page include Prime Volt 2 Go logo and phone number 818-555-0147
please use Knullshock fonts for the upper case letters and lower case letters as well attached is the link for the Comet Forge website for inspiration https://www.cometforgeusa.example/space-systems/solar/

Target Market(s)

residential solar clients

Industry/Entity Type

solar

Font styles to use
Other font styles liked:
• Knullshock

Colors

Designer to choose colors to be used in the design.

Requirements
Must have
• Knullshock Fonts inspired by Comet Forges website https://www.cometforgeusa.example/space-systems/solar/
Nice to have
• I would like to see a black background with white Knullshock lettering CAPITAL LETTERS and lower case letters
Should not have
• should not have solar panel images ,people get turn off if they see solar panels but they like batteries around here

```html
<!DOCTYPE html>
<html lang="en">
<head>
<meta charset="utf-8">
<title>Prime Volt 2 Go — Tri-fold Mailer</title>
<link href="https://fonts.googleapis.com/css2?family=Michroma&family=Poppins:wght@400;500;600;700&display=swap" rel="stylesheet">
<style>
  :root {
    --page-bg: #cfcfcc;
    --ink-black: #0b0b0b;
    --paper-white: #f4f4f4;
    --text-white: #ffffff;
    --text-muted: #d6d6d6;
    --brand-red: #e21f26;
    --deep-red: #5c0f10;
    --darkest-red: #1c0505;
    --mail-ink: #333333;
  }
  * { margin: 0; padding: 0; box-sizing: border-box; }
  html, body { width: 1111px; height: 1200px; overflow: hidden; }
  body {
    background: var(--page-bg);
    font-family: "Poppins", sans-serif;
    position: relative;
  }
  .brochure {
    position: absolute;
    left: 40px; top: 326px;
    width: 1032px; height: 548px;
    display: flex;
  }
  .panel { position: relative; width: 344px; height: 548px; overflow: hidden; }

  /* Inside flap */
  .panel--benefits { background: var(--ink-black); color: var(--text-white); padding: 56px 22px 0 22px; }
  .benefits__title {
    font-family: "Michroma", sans-serif;
    font-size: 16px; line-height: 26px; letter-spacing: 0.5px;
    text-transform: uppercase;
  }
  .benefits__intro { font-size: 8px; line-height: 12px; margin-top: 10px; color: var(--text-muted); width: 300px; }
  .benefits__tagline { font-size: 14.5px; font-weight: 600; margin-top: 30px; }
  .benefit-list { list-style: none; margin-top: 20px; }
  .benefit {
    display: flex; align-items: flex-start; gap: 12px;
    padding-bottom: 14px; margin-bottom: 14px; position: relative;
  }
  .benefit::after {
    content: ""; position: absolute; left: 0; bottom: 0; width: 300px; height: 1px;
    background: linear-gradient(90deg, var(--brand-red), rgba(226,31,38,0));
  }
  .benefit:last-child::after { display: none; }
  .benefit__icon { flex: 0 0 28px; width: 28px; height: 28px; }
  .benefit__title { font-size: 10.5px; font-weight: 600; line-height: 14px; }
  .benefit__text { font-size: 8px; line-height: 11px; color: var(--text-muted); }
  .testimonial { margin-top: 6px; font-size: 12px; line-height: 19px; width: 305px; }
  .testimonial__name { margin-top: 14px; font-size: 8.5px; font-weight: 600; line-height: 14px; }

  /* Mailing panel */
  .panel--mailing { background: var(--paper-white); color: var(--mail-ink); }
  .mailing__brand {
    position: absolute; left: 35px; top: 260px;
    transform: translate(-50%, -50%) rotate(-90deg);
    font-family: "Michroma", sans-serif; font-size: 27px; white-space: nowrap;
    color: var(--ink-black); font-weight: 400; -webkit-text-stroke: 0.6px var(--ink-black);
  }
  .rotated { position: absolute; transform-origin: top left; transform: rotate(90deg); white-space: nowrap; font-size: 7px; line-height: 10px; }
  .mailing__return { left: 182px; top: 285px; }
  .mailing__recipient { left: 309px; top: 200px; }
  .mailing__indicia {
    position: absolute; left: 222px; top: 39px; width: 45px; height: 62px;
    border: 1px solid var(--mail-ink);
  }
  .mailing__indicia span {
    position: absolute; left: 41px; top: 5px; transform-origin: top left; transform: rotate(90deg);
    font-size: 5px; line-height: 7px; white-space: nowrap;
  }
  .mailing__seal { position: absolute; left: 228px; top: 108px; width: 24px; height: 24px; border: 1px solid var(--mail-ink); }

  /* Cover */
  .panel--cover { background: var(--ink-black); color: var(--text-white); text-align: center; }
  .cover__bands { position: absolute; inset: 0; }
  .cover__kicker { position: absolute; top: 32px; width: 100%; font-size: 11px; }
  .cover__headline { position: absolute; top: 50px; width: 100%; font-size: 20px; line-height: 27px; }
  .cover__headline strong { font-weight: 600; }
  .cover__art {
    position: absolute; left: 42px; top: 112px; width: 268px; height: 216px;
    background: radial-gradient(ellipse at 45% 55%, #5a1214 0%, #2a2a2a 45%, var(--ink-black) 75%);
    border-radius: 8px;
  }
  .cover__brand {
    position: absolute; top: 428px; width: 100%;
    font-family: "Michroma", sans-serif; font-size: 15px; letter-spacing: 0.5px;
    -webkit-text-stroke: 0.4px var(--text-white);
  }
  .cover__phone {
    position: absolute; top: 468px; width: 100%;
    display: flex; justify-content: center; align-items: center; gap: 10px; font-size: 19px;
  }
  .cover__phone svg { width: 18px; height: 18px; }
  .cover__web { position: absolute; top: 502px; width: 100%; font-size: 9.5px; }
  .cover__web em { font-style: normal; color: var(--brand-red); }
</style>
</head>
<body>
<main class="brochure">

  <section class="panel panel--benefits">
    <h2 class="benefits__title">Your solar panels<br>can do more for you</h2>
    <p class="benefits__intro">Adding a battery to your home lets you prevent power outages and save money every month . Even better , you may qualify for a free battery system from the state</p>
    <h3 class="benefits__tagline">All the benefits. None of the costs.</h3>
    <ul class="benefit-list">
      <li class="benefit">
        <svg class="benefit__icon" viewBox="0 0 28 28"><circle cx="14" cy="14" r="14" fill="var(--brand-red)"/><path d="M15.5 6 9.5 15h4l-1.5 7 6.5-9.5h-4z" fill="#fff"/></svg>
        <div><p class="benefit__title">Secure reliable power</p><p class="benefit__text">your battery will keep your home powered through it all<br>wildfire shutoffs, and storms</p></div>
      </li>
      <li class="benefit">
        <svg class="benefit__icon" viewBox="0 0 28 28"><circle cx="14" cy="14" r="14" fill="var(--brand-red)"/><circle cx="14" cy="14" r="7" fill="#fff"/><text x="14" y="17.5" text-anchor="middle" font-family="Poppins, sans-serif" font-size="10" font-weight="700" fill="var(--brand-red)">$</text></svg>
        <div><p class="benefit__title">Lower electric bills by up to 90%</p><p class="benefit__text">Store surplus solar enery and switch to battery power<br>when rates are priceist.</p></div>
      </li>
      <li class="benefit">
        <svg class="benefit__icon" viewBox="0 0 28 28"><circle cx="14" cy="14" r="14" fill="var(--brand-red)"/><circle cx="14" cy="14" r="6" fill="none" stroke="#fff" stroke-width="3" stroke-dasharray="2.2 1.6"/><circle cx="14" cy="14" r="3.5" fill="none" stroke="#fff" stroke-width="2"/></svg>
        <div><p class="benefit__title">Full- service maintaince</p><p class="benefit__text">Heven-backed product and service support guaranteed</p></div>
      </li>
    </ul>
    <blockquote class="testimonial">" I'm in a high fire zone and wanted to do what i could to prevent outages, getting battery backup was a way to have some peace of mind</blockquote>
    <p class="testimonial__name">Lena R.<br>Topanga , CA</p>
  </section>

  <section class="panel panel--mailing">
    <p class="mailing__brand">PRIME VOLT 2 GO</p>
    <div class="mailing__indicia"><span>PRESORTED<br>FIRST CLASS<br>U.S. POSTAGE<br>PAID</span></div>
    <div class="mailing__seal" role="img" aria-label="Certification badge"></div>
    <address class="rotated mailing__return" style="font-style:normal">4800 Harbor Ave, Suite 210<br>Burbank, CA 91502</address>
    <address class="rotated mailing__recipient" style="font-style:normal">RT204 - 11863 T12 P1 P2<br><br>DANA WHITCOMBE<br>1420 ORCHARD LN<br>CASTAIC, CA 91384</address>
  </section>

  <section class="panel panel--cover">
    <svg class="cover__bands" viewBox="0 0 344 548" preserveAspectRatio="none" aria-hidden="true">
      <defs>
        <linearGradient id="coverBand" x1="0" y1="0" x2="0" y2="1">
          <stop offset="0" stop-color="var(--deep-red)"/>
          <stop offset="1" stop-color="var(--darkest-red)"/>
        </linearGradient>
      </defs>
      <polygon points="0,378 344,370 344,392 130,418 0,430" fill="var(--brand-red)"/>
      <polygon points="0,430 130,418 344,392 344,548 0,548" fill="url(#coverBand)"/>
    </svg>
    <p class="cover__kicker">Beat blackouts, save money</p>
    <h1 class="cover__headline" style="font-weight:400">You may qualify for a<br><strong>free battery system.</strong></h1>
    <div class="cover__art" role="img" aria-label="Illustration of a red home battery with a savings coin, a cloud and a utility grid connection"></div>
    <p class="cover__brand">PRIME VOLT 2 GO</p>
    <p class="cover__phone">
      <svg viewBox="0 0 18 18" aria-hidden="true"><circle cx="9" cy="9" r="9" fill="var(--brand-red)"/><path d="M6 4.5c.6-.3 1.1 0 1.4.6l.6 1.4c.2.5 0 .9-.4 1.2l-.5.4c.5 1.1 1.4 2 2.5 2.5l.4-.5c.3-.4.7-.6 1.2-.4l1.4.6c.6.3.9.8.6 1.4-.5 1.1-1.5 1.6-2.6 1.3C8 12.3 5.7 10 5 7.4c-.3-1.1.1-2.2 1-2.9z" fill="#fff"/></svg>
      818-555-0147
    </p>
    <p class="cover__web">www.<em>primevolt2go</em>.example</p>
  </section>

</main>
</body>
</html>
```